Banner ad series

We need a series of banner ads for 4 different digital products. The ads will drive traffic to these landing pages:
Relocate.set: http://pinnedtidygoods.example/relocatekit/
Treasures.file: http://pinnedtidygoods.example/digital-treasures-file/
Jumpstart Drill School: http://pinnedtidygoods.example/jumpstart-drill-school/
Vital Habits Drill School: http://pinnedtidygoods.example/vital-habits/

Banner Ad Sizes needed:
160x600, 728x90, 300x250

Text files with the copy/variations needed for each product are attached. In the text file - the first line of each option is the main headline. All other copy is support copy and OPTIONAL.

Target Market(s)

Our target market is a woman between the ages of 30-55 with kids. She's smart, working professionally and always on the lookout for products and services that will help her get more organized.

Industry/Entity Type

Digital

Requirements
Must have
• Pinned Tidy logo

```html
<!DOCTYPE html>
<html lang="en">
<head>
<meta charset="utf-8">
<title>Pinned Tidy – Jumpstart Drill School banner set</title>
<link rel="stylesheet" href="https://fonts.googleapis.com/css2?family=PT+Sans:wght@400;700&display=swap">
<style>
  :root {
    --stage: #4e3222;
    --green: #2f9414;
    --green-dark: #247a0d;
    --green-light: #8cc63f;
    --white: #ffffff;
    --logo-ink: #7ab51d;
    --logo-frame: #c9a0a8;
    --photo-light: #eef0ec;
    --photo-mid: #d9ddd5;
    --orange-top: #ffa233;
    --orange-bottom: #e86a00;
    --arrow-bg: #1f1f1f;
  }
  * { box-sizing: border-box; margin: 0; padding: 0; }
  html, body { width: 1200px; height: 800px; overflow: hidden; }
  body {
    background: var(--stage);
    font-family: "PT Sans", Arial, sans-serif;
    position: relative;
  }
  .banner { position: absolute; overflow: hidden; background: var(--green); color: var(--white); }
  .banner-art { position: absolute; inset: 0; }
  .logo-panel { position: absolute; background: var(--white); display: flex; align-items: center; justify-content: center; }
  .logo-frame {
    display: flex; align-items: center; gap: 8px;
    border: 2px dotted var(--logo-frame); border-radius: 6px;
    padding: 0 12px; background: var(--white);
  }
  .logo-mark { width: 12px; height: 12px; border-radius: 50%; background: var(--logo-ink); flex: none; }
  .logo-name { color: var(--logo-ink); font-weight: 400; font-size: 20px; white-space: nowrap; }
  .copy { position: absolute; text-align: center; text-transform: uppercase; font-weight: 700; }
  .copy .line-lead { display: block; }
  .rule { display: block; border-top: 1px dotted rgba(255,255,255,.7); margin: 0 auto; }
  .support { position: absolute; text-align: center; font-size: 14.5px; line-height: 1.15; }
  .cta {
    position: absolute; display: flex; align-items: center; justify-content: flex-end;
    gap: 8px; padding-right: 6px;
    border-radius: 22px; border: 2px solid #ffd7a8;
    background: linear-gradient(var(--orange-top), var(--orange-bottom));
    color: var(--white); font-weight: 700; font-size: 17px;
    box-shadow: 0 2px 3px rgba(0,0,0,.3);
  }
  .cta-arrow { width: 26px; height: 26px; flex: none; }

  /* 160x600 skyscraper */
  .skyscraper { left: 56px; top: 53px; width: 183px; height: 686px; }
  .skyscraper .logo-panel { left: 0; top: 0; width: 183px; height: 88px; }
  .skyscraper .logo-frame { width: 160px; height: 64px; }
  .skyscraper .copy { left: 0; width: 183px; top: 375px; }
  .skyscraper .support { left: 0; width: 183px; top: 553px; }
  .skyscraper .cta { left: 7px; top: 632px; width: 169px; height: 40px; }

  /* 300x250 medium rectangle */
  .rectangle { width: 343px; height: 286px; top: 232px; }
  .rectangle.first { left: 319px; }
  .rectangle.second { left: 689px; }
  .rectangle .logo-panel { left: 0; top: 0; width: 180px; height: 74px; background: transparent; }
  .rectangle .logo-frame { width: 162px; height: 64px; }
  .rectangle .copy { left: 0; width: 168px; top: 92px; }
  .rectangle .support { left: 0; width: 168px; top: 222px; }
  .rectangle .cta { left: 174px; top: 234px; width: 163px; height: 40px; }

  /* 728x90 leaderboard */
  .leaderboard { left: 273px; top: 577px; width: 832px; height: 103px; }
  .leaderboard .logo-panel { left: 0; top: 0; width: 175px; height: 103px; }
  .leaderboard .logo-frame { width: 158px; height: 68px; }
  .leaderboard .copy { left: 182px; width: 370px; top: 8px; }
  .leaderboard .support { left: 182px; width: 370px; top: 62px; }
  .leaderboard .cta { left: 635px; top: 40px; width: 168px; height: 41px; }
</style>
</head>
<body>

<!-- Skyscraper -->
<section class="banner skyscraper" aria-label="Jumpstart Drill School skyscraper banner">
  <svg class="banner-art" width="183" height="686" viewBox="0 0 183 686">
    <defs>
      <linearGradient id="sky-photo" x1="0" y1="0" x2="0" y2="1">
        <stop offset="0" stop-color="var(--photo-light)"/>
        <stop offset="1" stop-color="var(--photo-mid)"/>
      </linearGradient>
    </defs>
    <rect x="0" y="88" width="183" height="220" fill="url(#sky-photo)" role="img" aria-label="Photo of a tidy white wall organiser with files and pinned notes"/>
    <path d="M0 300 Q92 265 183 290 L183 686 L0 686 Z" fill="var(--green-light)"/>
    <path d="M0 308 Q92 275 183 298 L183 686 L0 686 Z" fill="var(--green)"/>
  </svg>
  <div class="logo-panel"><div class="logo-frame"><span class="logo-mark"></span><span class="logo-name">Pinned Tidy</span></div></div>
  <div class="copy">
    <span class="line-lead" style="font-size:22px">Now that it's</span>
    <span class="line-lead" style="font-size:18px;margin-top:2px">The new new year</span>
    <span class="rule" style="width:130px;margin-top:14px;margin-bottom:14px"></span>
    <span class="line-lead" style="font-size:21px">It's time to</span>
    <span class="line-lead" style="font-size:21px">Get organized!</span>
    <span class="rule" style="width:130px;margin-top:14px"></span>
  </div>
  <p class="support">Sign Up for the Jumpstart<br>Drill School &amp; Organize<br>your home AND your life</p>
  <div class="cta">Learn More!
    <svg class="cta-arrow" viewBox="0 0 26 26"><circle cx="13" cy="13" r="12" fill="var(--arrow-bg)" stroke="#fff" stroke-width="1.5"/><path d="M10.5 7.5 L16 13 L10.5 18.5" fill="none" stroke="#fff" stroke-width="3"/></svg>
  </div>
</section>

<!-- Medium rectangles -->
<section class="banner rectangle first" aria-label="Jumpstart Drill School rectangle banner">
  <svg class="banner-art" width="343" height="286" viewBox="0 0 343 286">
    <defs>
      <linearGradient id="rect-photo-a" x1="0" y1="0" x2="0" y2="1">
        <stop offset="0" stop-color="var(--photo-light)"/>
        <stop offset="1" stop-color="var(--photo-mid)"/>
      </linearGradient>
    </defs>
    <rect x="150" y="0" width="193" height="286" fill="url(#rect-photo-a)" role="img" aria-label="Photo of a tidy white wall organiser with files and pinned notes"/>
    <path d="M0 0 L230 0 Q178 90 186 286 L0 286 Z" fill="var(--green-light)"/>
    <path d="M0 0 L220 0 Q170 90 178 286 L0 286 Z" fill="var(--green)"/>
    <rect x="0" y="0" width="180" height="74" fill="var(--white)"/>
  </svg>
  <div class="logo-panel"><div class="logo-frame"><span class="logo-mark"></span><span class="logo-name">Pinned Tidy</span></div></div>
  <div class="copy">
    <span class="line-lead" style="font-size:21px">Now that it's</span>
    <span class="line-lead" style="font-size:16.5px;margin-top:1px">The new new year</span>
    <span class="rule" style="width:128px;margin-top:7px;margin-bottom:8px"></span>
    <span class="line-lead" style="font-size:20px">It's time to</span>
    <span class="line-lead" style="font-size:20px">Get organized!</span>
    <span class="rule" style="width:128px;margin-top:5px"></span>
  </div>
  <p class="support">Sign Up for the Jumpstart<br>Drill School &amp; Organize<br>your home AND your life</p>
  <div class="cta">Learn More!
    <svg class="cta-arrow" viewBox="0 0 26 26"><circle cx="13" cy="13" r="12" fill="var(--arrow-bg)" stroke="#fff" stroke-width="1.5"/><path d="M10.5 7.5 L16 13 L10.5 18.5" fill="none" stroke="#fff" stroke-width="3"/></svg>
  </div>
</section>

<section class="banner rectangle second" aria-label="Jumpstart Drill School rectangle banner">
  <svg class="banner-art" width="343" height="286" viewBox="0 0 343 286">
    <defs>
      <linearGradient id="rect-photo-b" x1="0" y1="0" x2="0" y2="1">
        <stop offset="0" stop-color="var(--photo-light)"/>
        <stop offset="1" stop-color="var(--photo-mid)"/>
      </linearGradient>
    </defs>
    <rect x="150" y="0" width="193" height="286" fill="url(#rect-photo-b)" role="img" aria-label="Photo of a tidy white wall organiser with files and pinned notes"/>
    <path d="M0 0 L230 0 Q178 90 186 286 L0 286 Z" fill="var(--green-light)"/>
    <path d="M0 0 L220 0 Q170 90 178 286 L0 286 Z" fill="var(--green)"/>
    <rect x="0" y="0" width="180" height="74" fill="var(--white)"/>
  </svg>
  <div class="logo-panel"><div class="logo-frame"><span class="logo-mark"></span><span class="logo-name">Pinned Tidy</span></div></div>
  <div class="copy">
    <span class="line-lead" style="font-size:21px">Now that it's</span>
    <span class="line-lead" style="font-size:16.5px;margin-top:1px">The new new year</span>
    <span class="rule" style="width:128px;margin-top:7px;margin-bottom:8px"></span>
    <span class="line-lead" style="font-size:20px">It's time to</span>
    <span class="line-lead" style="font-size:20px">Get organized!</span>
    <span class="rule" style="width:128px;margin-top:5px"></span>
  </div>
  <p class="support">Sign Up for the Jumpstart<br>Drill School &amp; Organize<br>your home AND your life</p>
  <div class="cta">Learn More!
    <svg class="cta-arrow" viewBox="0 0 26 26"><circle cx="13" cy="13" r="12" fill="var(--arrow-bg)" stroke="#fff" stroke-width="1.5"/><path d="M10.5 7.5 L16 13 L10.5 18.5" fill="none" stroke="#fff" stroke-width="3"/></svg>
  </div>
</section>

<!-- Leaderboard -->
<section class="banner leaderboard" aria-label="Jumpstart Drill School leaderboard banner">
  <svg class="banner-art" width="832" height="103" viewBox="0 0 832 103">
    <defs>
      <linearGradient id="leader-photo" x1="0" y1="0" x2="0" y2="1">
        <stop offset="0" stop-color="var(--photo-light)"/>
        <stop offset="1" stop-color="var(--photo-mid)"/>
      </linearGradient>
    </defs>
    <rect x="560" y="0" width="272" height="103" fill="url(#leader-photo)" role="img" aria-label="Photo of a tidy white wall organiser with files and hooks"/>
    <path d="M0 0 L600 0 Q568 50 584 103 L0 103 Z" fill="var(--green-light)"/>
    <path d="M0 0 L592 0 Q560 50 576 103 L0 103 Z" fill="var(--green)"/>
  </svg>
  <div class="logo-panel"><div class="logo-frame"><span class="logo-mark"></span><span class="logo-name">Pinned Tidy</span></div></div>
  <div class="copy">
    <span class="line-lead" style="font-size:20px">Now that it's the&nbsp; new new year</span>
    <span class="line-lead" style="font-size:23px;margin-top:1px">It's time to get organized!</span>
  </div>
  <p class="support">Sign Up for the JumpstartDrill School &amp; Organize your<br>home AND your life</p>
  <div class="cta">Learn More!
    <svg class="cta-arrow" viewBox="0 0 26 26"><circle cx="13" cy="13" r="12" fill="var(--arrow-bg)" stroke="#fff" stroke-width="1.5"/><path d="M10.5 7.5 L16 13 L10.5 18.5" fill="none" stroke="#fff" stroke-width="3"/></svg>
  </div>
</section>

</body>
</html>
```